Website Redesign for a faith-based, not-for-profit health and human services organization

New website design for the Harvest Hope Outreach House.
- Current site: www.hhohbriel.org -
We are looking for a nice clean, simple, friendly-yet-elegant website layout.
Colors are #f5eed5 (cream), #FFFFFF (white), and all logo colors.
Design a layout for home page
Design a layout for general layouts
-layout only no html needed (preferably a high res PSD file format) -
Main menu should be along top with side navigation for submenu, no side menu on home page.
Also would be open to seeing some updated colors on the logo design, currently the colors are slightly outdated. The Vine of Plenty quilt design fits the organization’s mission and the rural farming / Amish-Mennonite-Brethren community around us.

ADDITIONAL PAGES AND MENU STRUCTURE ON NEW SITE

- How to Help
... Volunteer
... Donate Time
... Donate Money
... Donate Supplies
... Current Needs

- Programs

- News & Events
... Upcoming Events
... Upcoming Fundraisers
... Newsletter

- Our Partners

- About Us
... Overview
... Mission
... Staff Directory
... Board of Directors
... Annual Reports

- Contact

Our annual special event is Gather at the Hearth and should be integrated into the home page - see attached logos and banner

Websites with elements we like (from organizations doing similar work), each for a different reason....

1. http://www.kinbridgeroutes.org
Good design, color, clarity on this site. Multi-dimensional, photos...easy interaction, etc.

2. http://endemptyplates.org
Quite simple, nothing fancy, but some good basic stuff here, and pretty easy to navigate...

3. http://www.townfolkhub.org
Intrigued by the bulletin board design and the way they have their programs broken down to show impact, needs, etc. It has a lot of good information, but is really too verbose, some of the print is too small, etc. Not perfect, but some interesting design elements.

4. http://sharedlarder.org
Site is boring and not very well designed, but it has some of the features that we would like to see at the top, donations, partners, etc.

5. http://www.bellmerefoodshelf.org
Too many listings on the sidebar - needs to be cleaner & simpler, but a lot of good information and we like the way they show volunteer photos on the Thanks to Our Helpers page...

About
Harvest Hope Outreach House ("HHOH" or “the Center”) is a faith-based non-for-profit health and human services organization that exists as an outreach of and for the Ordell-Bray Area School District.
Tagline: Mercy at Work (we work to serve the needs of the ‘least of these’ with compassion).

Mission
Our mission is to see lives transformed and the community enhanced by encouraging the oppressed, defending the cause of the weak and maintaining the rights of the poor - bringing together the resources of a caring community as a demonstration of the good news of Christ.

Company Overview
Harvest Hope Outreach House works closely with the community in which it serves. A tremendous value is placed upon the partnerships that have formed with caring people within the community and with organizations that share the goal of bringing together resources to help those who need it most. Individuals, volunteers, churches, corporations, foundations, and government sources all pull together to help make our mission possible.

Since 1996 the Harvest Hope Outreach House has collaboratively worked to see our community enhanced, adapting programs and services to meet the changing needs of the community.

Target Market(s)

people needing assistance in local community

Industry/Entity Type

Government

Requirements
Must have
• Good social button integration
Should not have
• No Find Us page like old website it is not needed

```html
<!DOCTYPE html>
<html lang="en">
<head>
<meta charset="utf-8">
<title>Harvest Hope Outreach House</title>
<link href="https://fonts.googleapis.com/css2?family=Lora:wght@400;700&family=Open+Sans:wght@400;600;700&display=swap" rel="stylesheet">
<style>
:root{
  --page-bg:#ecebe6;
  --paper:#ffffff;
  --cream:#f5eed5;
  --brand-red:#a3262a;
  --green-dark:#2f5a2c;
  --green:#4c7d3a;
  --green-light:#7ea35c;
  --text:#555555;
  --muted:#8a8a8a;
  --rule:#dcd8cc;
  --caption:rgba(30,30,30,.72);
}
*{box-sizing:border-box;margin:0;padding:0}
html,body{width:891px;height:1200px;overflow:hidden}
body{background:var(--page-bg);font-family:"Open Sans",Arial,sans-serif;color:var(--text);font-size:10px;line-height:1.5}
.page{position:absolute;left:72px;top:0;width:752px;height:1200px;background:var(--paper);box-shadow:0 0 10px rgba(0,0,0,.12)}
.brand{position:absolute;left:18px;top:20px;display:flex;align-items:center;gap:12px}
.brand-mark{width:62px;height:62px;background:var(--brand-red)}
.brand-name{font-family:"Lora",Georgia,serif;font-weight:700;color:var(--brand-red);font-size:21px;line-height:1.08;width:190px}
.search{position:absolute;right:22px;top:36px;width:128px;height:22px;border:1px solid var(--rule);border-radius:3px;display:flex;align-items:center;justify-content:space-between;padding:0 7px;color:var(--muted);font-size:10px}
.call{position:absolute;right:22px;top:72px;display:flex;align-items:center;gap:6px;font-size:14px;color:var(--text)}
.call strong{color:var(--green-dark);font-weight:700}
.main-nav{position:absolute;left:12px;right:12px;top:125px;height:32px;background:linear-gradient(var(--green-light),var(--green) 55%,var(--green-dark));display:flex;border-radius:2px}
.main-nav a{flex:1;color:#fff;text-decoration:none;font-size:12px;font-weight:600;display:flex;align-items:center;justify-content:center;border-right:1px solid rgba(255,255,255,.25)}
.main-nav a:last-child{border-right:0}
.main-nav a.active{background:rgba(255,255,255,.18)}
.slider{position:absolute;left:12px;right:12px;top:170px;height:275px;background:linear-gradient(160deg,#b9c7d6,#8fa27c 55%,#d8d1c0);overflow:hidden}
.slider-caption{position:absolute;left:0;right:0;bottom:18px;height:32px;background:var(--caption);color:#fff;font-size:13px;font-weight:600;display:flex;align-items:center;padding-left:40px}
.slider-arrow{position:absolute;top:118px;width:26px;height:36px;background:rgba(0,0,0,.4);display:flex;align-items:center;justify-content:center}
.slider-arrow.prev{left:0}.slider-arrow.next{right:0}
h2{font-family:"Lora",Georgia,serif;color:var(--brand-red);font-weight:700}
.welcome{position:absolute;left:16px;top:462px;width:420px}
.welcome h2{font-size:20px;margin-bottom:8px}
.welcome p{font-size:10px;line-height:1.55}
.btn{display:inline-block;background:var(--green-dark);color:#fff;font-size:9px;padding:3px 12px;border-radius:3px;margin-top:8px}
.welcome-photo{position:absolute;left:442px;top:512px;width:134px;height:112px;background:linear-gradient(135deg,#a9b58c,#6f8a56)}
.event-poster{position:absolute;left:590px;top:470px;width:148px;height:540px;background:linear-gradient(180deg,#36412b,#5d6e3a 30%,#b46a2a 60%,#2c2b26)}
.cards{position:absolute;left:16px;top:660px;width:556px;display:flex;gap:18px}
.card{flex:1}
.card h2{font-size:15px;margin-bottom:8px}
.card-body{background:var(--cream);border:1px solid var(--rule);padding:10px 12px 8px;height:118px;font-size:9.5px;line-height:1.5}
.date{display:block;color:var(--brand-red);font-size:9px;margin-top:6px}
.card-more{text-align:center;margin-top:6px}
.card-more span{display:inline-block;border:1px solid var(--rule);background:#f7f7f4;color:var(--muted);font-size:8.5px;padding:2px 14px;border-radius:10px}
.article{position:absolute;left:16px;width:556px;display:flex;gap:14px;border-top:1px solid var(--rule);padding-top:12px}
.article.one{top:890px}
.article.two{top:1020px}
.article-label{width:110px;height:90px;display:flex;flex-direction:column;align-items:center;justify-content:flex-end}
.article-label h2{font-size:14px}
.article-thumb{width:110px;height:80px;flex:none}
.article-thumb.volunteers{background:linear-gradient(135deg,#c6b58a,#7a8c5a)}
.article-thumb.event{background:linear-gradient(135deg,#c8452f,#e6b34a)}
.article-text{flex:1;font-size:9.5px;line-height:1.55;padding-top:4px}
.article-text .btn{margin-top:4px}
.newsletter{position:absolute;left:590px;top:1025px;width:148px;height:100px;background:var(--green-dark);color:#fff;padding:10px 12px}
.newsletter h2{color:#fff;font-size:15px;margin-bottom:4px}
.newsletter p{font-size:9px;margin-bottom:8px}
.newsletter-form{display:flex;gap:4px}
.newsletter-form span:first-child{flex:1;height:18px;background:#fff;border-radius:2px}
.newsletter-form span:last-child{background:var(--green-light);font-size:8.5px;font-weight:700;padding:2px 6px;border-radius:2px}
.site-footer{position:absolute;left:16px;right:16px;top:1144px;border-top:1px solid var(--rule);padding-top:10px;font-size:9px;color:var(--muted)}
.footer-links a{color:var(--text);text-decoration:none}
.social{position:absolute;right:0;top:14px;display:flex;gap:6px}
.social span{width:16px;height:16px;border-radius:50%;background:var(--green)}
</style>
</head>
<body>
<div class="page">
  <header>
    <div class="brand">
      <div class="brand-mark"></div>
      <div class="brand-name">Harvest Hope Outreach House</div>
    </div>
    <div class="search">Search
      <svg width="10" height="10" viewBox="0 0 10 10"><circle cx="4" cy="4" r="3" fill="none" stroke="#888" stroke-width="1.3"/><line x1="6.2" y1="6.2" x2="9.3" y2="9.3" stroke="#888" stroke-width="1.3"/></svg>
    </div>
    <div class="call">
      <svg width="14" height="14" viewBox="0 0 14 14"><path d="M3 1l2.5 3-1.5 1.5c.8 1.8 2.2 3.2 4 4L9.5 8l3 2.5-1.5 2.5C6 12.5 1.5 8 1 2.5z" fill="#2f5a2c"/></svg>
      Call us <strong>(555) 014-2260</strong>
    </div>
    <nav class="main-nav">
      <a class="active">Home</a><a>How to Help</a><a>Programs</a><a>News &amp; Events</a><a>Our Partners</a><a>About us</a><a>Contact</a>
    </nav>
  </header>

  <section class="slider" role="img" aria-label="Group photo of volunteers at the food drive">
    <div class="slider-arrow prev"><svg width="10" height="14"><path d="M8 1L2 7l6 6" stroke="#fff" stroke-width="2" fill="none"/></svg></div>
    <div class="slider-arrow next"><svg width="10" height="14"><path d="M2 1l6 6-6 6" stroke="#fff" stroke-width="2" fill="none"/></svg></div>
    <div class="slider-caption">Harvest Hope Outreach House's - Route Carriers Food Drive</div>
  </section>

  <section class="welcome">
    <h2>Welcome to HHOH</h2>
    <p>Harvest Hope Outreach House serves families across our rural community with food, care and a warm welcome. Neighbors, churches and volunteers join together each week to meet real needs with compassion. Come see how a small gift of time or supplies can change a life close to home and bring hope to those who need it most.</p>
    <span class="btn">View more</span>
  </section>
  <div class="welcome-photo" role="img" aria-label="Photo of volunteers sorting donations"></div>

  <aside class="event-poster" role="img" aria-label="Gather at the Hearth farm to table dinner and auction event poster"></aside>

  <section class="cards">
    <article class="card">
      <h2>A thought</h2>
      <div class="card-body">Small acts of kindness, offered faithfully, grow into a harvest of hope for neighbors who feel forgotten.<span class="date">February 25 2013</span></div>
      <div class="card-more"><span>Read more</span></div>
    </article>
    <article class="card">
      <h2>A prayer</h2>
      <div class="card-body">Lord, give us open hands and willing hearts to serve every family that walks through our doors this week.<span class="date">February 25 2013</span></div>
      <div class="card-more"><span>Read more</span></div>
    </article>
    <article class="card">
      <h2>A urgent need</h2>
      <div class="card-body">Our pantry shelves are low on canned fruit, cereal and diapers. Drop off donations Monday through Friday.<span class="date">February 25 2013</span></div>
      <div class="card-more"><span>Read more</span></div>
    </article>
  </section>

  <section class="article one">
    <div class="article-label"><h2>Latest Article</h2></div>
    <div class="article-thumb volunteers" role="img" aria-label="Photo of volunteers packing meal boxes"></div>
    <div class="article-text">Volunteers packed over four hundred meal boxes for local families this month. Read about the people who made it happen and how you can join the next packing day.<span class="date">February 25 2013</span></div>
  </section>

  <section class="article two">
    <div class="article-thumb event" role="img" aria-label="Gather at the Hearth event emblem"></div>
    <div class="article-text">Tickets are now on sale for Gather at the Hearth, our annual farm to table dinner and auction supporting programs across the district.<span class="date">February 25 2013</span></div>
  </section>

  <aside class="newsletter">
    <h2>Newsletter</h2>
    <p>Sign up for news and event updates.</p>
    <div class="newsletter-form"><span></span><span>SUBMIT</span></div>
  </aside>

  <footer class="site-footer">
    <div class="footer-links"><a>Home</a> | <a>How to Help</a> | <a>Programs</a> | <a>News &amp; Events</a> | <a>Our Partners</a> | <a>About us</a> | <a>Contact</a></div>
    <div>Copyright © 2013 www.hhohbriel.org All rights reserved.</div>
    <div class="social"><span></span><span></span><span></span><span></span></div>
  </footer>
</div>
</body>
</html>
```